Covid 19 Exit Strategy one page brochure

I would like to design, and will need URGENT help, a brochure detailing a Covid 19 Exit Strategy plan. This brochure will need to be understood easily and the graphics inside should make it easy for people to understand without reading the entire text. This project is quite urgent and needs to be completed THIS WEEK - by Saturday may 16th at the latest. I am attaching two examples. I will provide the text.

```html
<!DOCTYPE html>
<html lang="en">
<head>
<meta charset="utf-8">
<title>COVID-19 Phased Exit Strategy</title>
<link rel="stylesheet" href="https://fonts.googleapis.com/css2?family=Lexend:wght@400;700&family=Mulish:wght@400&display=swap">
<style>
  :root {
    --ink-black: #05080b;
    --deep-teal: #0c3a46;
    --teal-glow: #1d5e6c;
    --crimson: #a3111e;
    --crimson-dark: #5d0710;
    --blood: #7a0a15;
    --electric-blue: #1a6dbb;
    --navy: #0f2c6e;
    --white: #ffffff;
  }
  html, body {
    margin: 0;
    padding: 0;
    width: 861px;
    height: 1200px;
    overflow: hidden;
    background: var(--ink-black);
  }
  .brochure {
    position: relative;
    width: 861px;
    height: 1200px;
    overflow: hidden;
    background: linear-gradient(160deg, var(--deep-teal) 0%, #0a2a33 45%, var(--ink-black) 80%);
    color: var(--white);
  }
  .hero-photo {
    position: absolute;
    left: 360px;
    top: 300px;
    width: 501px;
    height: 774px;
    background:
      radial-gradient(ellipse 45% 40% at 85% 70%, rgba(190, 215, 220, 0.55), rgba(190, 215, 220, 0) 70%),
      radial-gradient(ellipse 60% 50% at 75% 45%, var(--teal-glow), rgba(12, 58, 70, 0) 75%),
      radial-gradient(circle 70px at 50% 78%, rgba(120, 20, 30, 0.45), rgba(120, 20, 30, 0) 100%);
  }
  .shapes {
    position: absolute;
    inset: 0;
  }
  .footer-band {
    position: absolute;
    left: 0;
    top: 1074px;
    width: 861px;
    height: 126px;
    background: linear-gradient(90deg, var(--blood) 0%, var(--crimson-dark) 55%, #3e050b 100%);
  }
  .title {
    position: absolute;
    left: 0;
    width: 861px;
    top: 128px;
    margin: 0;
    text-align: center;
    font-family: "Lexend", sans-serif;
  }
  .title-main {
    display: block;
    font-weight: 700;
    font-size: 58px;
    line-height: 62px;
    letter-spacing: -1px;
    padding-left: 6px;
  }
  .title-sub {
    display: block;
    font-weight: 400;
    font-size: 40.5px;
    line-height: 48px;
    margin-top: 6px;
    padding-left: 7px;
  }
  .copy {
    position: absolute;
    margin: 0;
    font-family: "Mulish", sans-serif;
    font-size: 16.4px;
    line-height: 26px;
    white-space: nowrap;
  }
  .copy-intro {
    left: 49px;
    top: 358px;
  }
  .copy-conditions {
    left: 154px;
    top: 929px;
  }
</style>
</head>
<body>
<main class="brochure">
  <div class="hero-photo" role="img" aria-label="Photograph of a person wearing a white respirator mask, with floating coronavirus particles"></div>

  <svg class="shapes" width="861" height="1200" viewBox="0 0 861 1200" aria-hidden="true">
    <defs>
      <linearGradient id="crimsonSweep" x1="0" y1="1" x2="1" y2="0">
        <stop offset="0" stop-color="#8d0c18"/>
        <stop offset="0.5" stop-color="#a3111e"/>
        <stop offset="1" stop-color="#6a0810"/>
      </linearGradient>
      <linearGradient id="blueStripe" x1="0" y1="1" x2="1" y2="0">
        <stop offset="0" stop-color="#0d4f96"/>
        <stop offset="1" stop-color="#1a6dbb"/>
      </linearGradient>
    </defs>
    <polygon class="band-top-left" points="0,0 290,0 0,330" fill="#0d3340"/>
    <polygon class="band-navy-top" points="250,34 300,34 0,380 0,330" fill="#0f2c6e"/>
    <polygon class="band-crimson" points="0,381 344,0 861,0 861,95 0,900" fill="url(#crimsonSweep)"/>
    <polygon class="band-crimson-sheen" points="300,0 340,0 120,250 80,250" fill="#c0202d" opacity="0.35"/>
    <polygon class="band-blue" points="794,164 834,164 503,526 466,526" fill="url(#blueStripe)"/>
    <polygon class="band-crimson-light" points="620,164 800,164 560,430 380,430" fill="#b0182a" opacity="0.25"/>
    <polygon class="band-lower-red" points="0,760 300,663 0,980" fill="#8f0d19" opacity="0.9"/>
    <polygon class="stripe-red" points="280,663 305,663 0,1000 0,972" fill="#c42130" opacity="0.55"/>
    <polygon class="band-navy-lower" points="292,757 300,757 0,1050 0,1040" fill="#0f2c6e"/>
    <polygon class="band-navy-wide" points="262,800 295,800 0,1074 0,1040" fill="#0f2c6e" opacity="0.9"/>
    <polygon class="band-dark-wedge" points="0,1074 290,800 430,1074" fill="#05080b" opacity="0.6"/>
    <polygon class="band-mask-shadow" points="460,640 861,1060 861,1074 430,1074" fill="#05080b" opacity="0.35"/>
  </svg>

  <div class="footer-band"></div>

  <h1 class="title">
    <span class="title-main">COVID-19</span>
    <span class="title-sub">PHASED EXIT STRATEGY</span>
  </h1>

  <p class="copy copy-intro">Pandemics have, historically, seen their end both<br>medically - via herd immunity or immunizations.<br>And while there are several clinical trials<br>underway for potential Covid-19 vaccines, we<br>are still a long way from deploying an effective<br>vaccine and one that will stand the test of time<br>as the virus changes. Covid-19 pandemic will be<br>considered 'ended' when there are only<br>occasional traces of localized cases that are<br>quickly contained in specific locations.,</p>

  <p class="copy copy-conditions">Today and in the absence of an effective vaccine(s) and for the<br>re-opening of the economies and social activities to be successful,<br>it is critical that the following basic conditions be in place before<br>any lockdowns are lifted and before social activities resume:</p>
</main>
</body>
</html>
```